DRIFTMOOR, Music and Science festival, needs a poster for 2018

DRIFTMOOR Leiden is a festival that bridges classical music and science in the Kestrel Bio Science Park (The Netherlands). We celebrate our second edition on the 5 & 6 October 2018. This unique cultural product is a collaboration of bio tech companies and University Ostbrook to deliver an original programme where science is the entry point to discover classical music on futuristic locations.

We want a poster to reflect on the duality science-music. This poster will be used in print and also as the branding foundation for other materials (web, social media, flyers, programmes, etc)

The poster has to use this image:

https://www.filecrate-example.com/s/q2rt7wn4pz81kdx/stockvault_412083967.jpg?dl=0
https://www.filecrate-example.com/s/h5mc9vb2xe63jtu/stockvault_412083967.eps?dl=0

We attach the poster from last year, just as a reference, and also the logo

Target Market(s)

Educated adults 25-70 yo

Industry/Entity Type

Festival

Font styles to use
Serif
Sans Serif

Colors

Designer to choose colors to be used in the design.

Requirements
Must have
• Vertical
• Graphic material that we can use for web design, social media, brouchure...
Nice to have
• Impactful image, music and science are stimulating for the brain

```html
<!DOCTYPE html>
<html lang="en">
<head>
<meta charset="utf-8">
<title>DRIFTMOOR 2018 – Classical Music &amp; Science</title>
<link rel="stylesheet" href="https://fonts.googleapis.com/css2?family=Arvo:wght@400;700&family=Roboto+Condensed:wght@400;700&display=swap">
<style>
  :root {
    --backdrop: #e4e4e6;
    --paper: #ffffff;
    --plum: #8b3a8f;
    --magenta: #d6267f;
    --rose: #e8407a;
    --pink-soft: #f4a3b4;
    --orange: #f27a2a;
    --yellow: #f5c94a;
    --sky: #7ab8e8;
    --leaf: #5aa05a;
    --navy: #1f2a4d;
    --ink-grey: #555a66;
    --sponsor-ink: #3a3f52;
    --rule: #d9d9dd;
    --brain-dark: #2e2e2e;
    --brain-mid: #8a8a8a;
    --brain-light: #e2e2e2;
  }
  * { margin: 0; padding: 0; box-sizing: border-box; }
  html, body { width: 1200px; height: 1200px; overflow: hidden; background: var(--backdrop); }
  .poster {
    position: absolute; left: 153px; top: 20px;
    width: 894px; height: 1160px;
    background: var(--paper);
    box-shadow: 0 6px 24px rgba(0,0,0,.15);
    overflow: hidden;
  }
  .illustration-flight {
    position: absolute; left: 0; top: 0; width: 894px; height: 620px;
  }
  .illustration-brain {
    position: absolute; left: 93px; top: 530px; width: 413px; height: 459px;
    border-radius: 50% 50% 46% 46% / 62% 62% 38% 38%;
    background: radial-gradient(ellipse 70% 60% at 50% 45%, var(--brain-light), var(--brain-mid) 55%, var(--brain-dark));
  }
  .title {
    position: absolute; left: 65px; top: 58px;
    font-family: "Arvo", serif; font-weight: 700;
    font-size: 52px; line-height: 58px; letter-spacing: 0;
    background: linear-gradient(90deg, var(--plum), var(--magenta) 70%, var(--rose));
    -webkit-background-clip: text; background-clip: text; color: transparent;
    white-space: nowrap;
  }
  .date { position: absolute; font-family: "Arvo", serif; line-height: 1; }
  .date-day-one { left: 592px; top: 636px; font-size: 84px; font-weight: 700; color: var(--magenta); }
  .date-day-two { left: 588px; top: 700px; font-size: 92px; font-weight: 700; color: var(--orange); }
  .date-amp { left: 551px; top: 712px; font-size: 44px; font-weight: 700; color: var(--sky); }
  .date-month { left: 656px; top: 643px; font-size: 74px; font-weight: 400; color: var(--pink-soft); letter-spacing: 1px; }
  .date-year { left: 656px; top: 718px; font-size: 72px; font-weight: 400; color: var(--yellow); }
  .brand { position: absolute; left: 565px; top: 870px; font-family: "Roboto Condensed", sans-serif; color: var(--navy); display: flex; gap: 14px; align-items: flex-start; }
  .brand-mark { width: 56px; height: 56px; border-radius: 50%; background: var(--navy); flex: none; margin-top: 4px; }
  .brand-name { font-size: 30px; font-weight: 700; letter-spacing: 1px; line-height: 34px; }
  .brand-tagline { font-size: 10px; margin-top: 2px; }
  .brand-url { font-size: 18px; margin-top: 10px; color: var(--ink-grey); }
  .sponsors {
    position: absolute; left: 0; bottom: 0; width: 100%; height: 133px;
    border-top: 6px solid var(--rule);
    display: flex; align-items: center; justify-content: space-around;
    padding: 0 24px;
    font-family: "Roboto Condensed", sans-serif; color: var(--sponsor-ink);
  }
  .sponsor { display: flex; align-items: center; gap: 6px; font-size: 13px; font-weight: 700; line-height: 1.1; }
  .sponsor-square { width: 22px; height: 22px; background: var(--sponsor-ink); }
  .sponsor-circle { width: 22px; height: 22px; border-radius: 50%; background: var(--sponsor-ink); }
  .sponsor-small { font-size: 8px; }
</style>
</head>
<body>
  <main class="poster">
    <svg class="illustration-flight" viewBox="0 0 894 620" role="img" aria-label="Colourful watercolour butterflies and musical notes rising out of the opened brain towards the upper right">
      <defs>
        <linearGradient id="flight-tone" x1="0.3" y1="1" x2="0.8" y2="0">
          <stop offset="0" stop-color="#e8407a"/>
          <stop offset="0.45" stop-color="#d6267f"/>
          <stop offset="0.75" stop-color="#f27a2a"/>
          <stop offset="1" stop-color="#5aa05a"/>
        </linearGradient>
        <filter id="flight-soft" x="-20%" y="-20%" width="140%" height="140%">
          <feGaussianBlur stdDeviation="22"/>
        </filter>
      </defs>
      <path d="M250 600 C180 470 60 420 55 350 C120 300 300 330 420 290 C560 240 560 120 640 90 C720 60 820 60 860 80 C870 180 800 260 700 330 C600 420 520 520 470 600 Z"
            fill="url(#flight-tone)" opacity="0.55" filter="url(#flight-soft)"/>
    </svg>
    <div class="illustration-brain" role="img" aria-label="Black and white drawing of a brain opened by a zipper"></div>

    <h1 class="title">CLASSICAL<br>MUSIC &amp; SCIENCE<br>IN HET KESTREL BIO<br>SIENCE PARK</h1>

    <div class="date date-day-one">5</div>
    <div class="date date-amp">&amp;</div>
    <div class="date date-day-two">6</div>
    <div class="date date-month">OCT</div>
    <div class="date date-year">2018</div>

    <div class="brand">
      <span class="brand-mark"></span>
      <div class="brand-text">
        <p class="brand-name">DRIFTMOOR</p>
        <p class="brand-tagline">Klassieke Muziek in het Kestrel Bio Science Park</p>
        <p class="brand-url">www.driftmoorkestrel.nl</p>
      </div>
    </div>

    <footer class="sponsors">
      <div class="sponsor"><span class="sponsor-square"></span>Kestrel</div>
      <div class="sponsor">Kestrel Ontdekt</div>
      <div class="sponsor">KESTREL<br>BIO SCIENCE<br>PARK</div>
      <div class="sponsor"><span class="sponsor-circle"></span>Universiteit<br>Ostbrook</div>
      <div class="sponsor">Stichting<br>Veldmanfonds</div>
      <div class="sponsor">Gravin van Haersma<br>Stichting</div>
      <div class="sponsor sponsor-small">MAREN ROSKAM<br>FOUNDATION</div>
    </footer>
  </main>
</body>
</html>
```